Website Creation for Kesto Course 2025 by Lon Varick "The Girl Who Painted Her Sky"

Project Title: "Kesto" Course Design Brief – Website design Build on Tilda
Client: Pebble Lantern Education
Course Title: Kesto by Lon Varick – The Girl Who Painted Her Sky
Logo: Lon Varick Logo
Course price: TBA
Overview:
We are seeking a designer to create cohesive and professional design assets for a new online course called Kesto. This transformative program combines neuroscience, emotional wellness, and ancient meditation practices to guide users through a journey of self-healing. We want the design to feel scientific yet spiritual, with clean, modern aesthetics that also convey depth and transformation. We use Tilda as our website builder so we need a design that can be easily transposed to that platform.
We require a visually compelling and dynamic banner image for the course webpage hero section (desktop and mobile versions)
We also require 7 x Individual thumbnail designs for each chakra meditation that will accompany the course with a workbook that will be designed in house (aligned with energy centre themes / Solfeggio frequencies / cosmic and sacred geometry)
Visual Direction:
• Clean, modern design with dark elements that balance science and spirituality.
• Soft gradients, energetic colors for chakras, and subtle abstract patterns or sacred geometry.
• Imagery could include brain neural networks, energy centres, or serene meditative figures and sacred geometry.
Course Themes to Inspire Design:
• Neuroplasticity and brain rewiring
• Emotional trauma and healing
• Meditation and Solfeggio frequencies
• Mind-body-spirit connection
• Empowerment and transformation
Lesson Breakdown:
• Lesson 1: The Science of Meditation & the Mind-Body Connection
• Lesson 2: Lon Varick’s Personal Healing & Neuroplasticity
• Lesson 3: Emotional Stress and Disease
• Lesson 4: ZRM (Zonal Ribbon Merge) Process
• Lesson 5: Solfeggio Frequencies & Chakra Healing
Target Audience:
Adult women 40 to 60 years old interested in healing illness, improving mental health, improving relationships, improving personal development, alternative healing, and meditation.

self development, meditation, healing

1 page

• futurapt

• branding copy used with relevant imagery and brand colours Stone #FAF0EA Sand #E2B9A5 Steel Blue #4F5266 Navy #2B243A Black: #000000 and Futura PT font
• chakra symbols and cosmic aesthetics with informational psychographics
• bright bold colours that don't match our branding

```html
<!DOCTYPE html>
<html lang="en">
<head>
<meta charset="utf-8">
<title>Kesto 2025 — Lon Varick</title>
<link href="https://fonts.googleapis.com/css2?family=Roboto:wght@400;500;700&family=Quicksand:wght@400;500;600&display=swap" rel="stylesheet">
<style>
:root{
  --navy:#0e1238;
  --gold:#c0950f;
  --dark:#1d1d1f;
  --white:#ffffff;
  --ink:#111111;
  --muted:#3a3a3a;
  --card-bg:#f7f7f7;
}
*{margin:0;padding:0;box-sizing:border-box}
html,body{width:1200px;height:5059px;overflow:hidden}
body{position:relative;background:var(--white);font-family:"Quicksand",sans-serif;color:var(--ink)}
.abs{position:absolute}
.center{text-align:center}
.heading{font-family:"Roboto",sans-serif;font-weight:700;color:var(--ink)}

/* hero */
.hero{left:0;top:0;width:1200px;height:686px;background:radial-gradient(ellipse at 50% 35%,#7a4a8e 0%,#4a3456 30%,#2a2530 60%,#1b1b1e 100%)}
.brand{left:110px;top:62px;font-family:"Quicksand",sans-serif;font-weight:600;font-size:12px;letter-spacing:2px;color:var(--white);display:flex;align-items:center;gap:8px}
.brand-mark{width:10px;height:10px;border:1px solid var(--white)}
.nav{top:64px;font-family:"Quicksand",sans-serif;font-weight:500;font-size:13px;color:var(--white)}
.nav.active{color:var(--gold)}
.btn-contact{left:949px;top:51px;width:139px;height:41px;background:var(--white);color:var(--ink);font-family:"Roboto",sans-serif;font-weight:700;font-size:13px;line-height:41px;text-align:center}
.hero-title{left:0;width:1200px;top:200px;font-family:"Roboto",sans-serif;font-weight:500;font-size:40px;letter-spacing:3px;line-height:60px;color:var(--white);text-align:center}
.hero-sub{left:0;width:1200px;top:337px;font-size:14px;color:var(--white);text-align:center}
.stat{top:460px;width:220px;text-align:center;color:var(--white)}
.stat h3{font-family:"Roboto",sans-serif;font-weight:500;font-size:31px;line-height:42px;height:42px}
.stat .by{font-family:"Roboto",sans-serif;font-weight:500;font-size:12px;margin-top:-8px;height:14px}
.stat hr{border:0;border-top:2px solid rgba(255,255,255,.75);margin-top:12px}
.stat p{font-size:14px;line-height:22px;margin-top:24px}

/* about */
.section-title{left:0;width:1200px;font-family:"Roboto",sans-serif;font-weight:700;font-size:37px;text-align:center;color:var(--ink)}
.lede{left:210px;width:780px;font-size:15px;line-height:27.5px;text-align:center;color:var(--muted)}
.lesson{color:var(--white);padding:0 20px 18px;display:flex;flex-direction:column;justify-content:flex-end}
.lesson.navy{background:var(--navy)}
.lesson b{font-family:"Quicksand",sans-serif;font-weight:600;font-size:16px;margin-bottom:10px}
.lesson span{font-size:14px;line-height:25px;font-weight:500}

/* chakra */
.book{top:2492px;width:300px;height:421px;background:var(--card-bg)}
.book .cover{position:absolute;left:72px;top:54px;width:160px;height:226px}
.book .cap{position:absolute;left:0;bottom:0;width:100%;height:95px;background:var(--navy);color:var(--white);text-align:center}
.book .cap h4{font-family:"Quicksand",sans-serif;font-weight:500;font-size:20px;margin-top:18px}
.book .cap p{font-size:14px;margin-top:12px}
.book.active{border:1px solid var(--gold)}
.book.active .cap{background:var(--gold)}
.arrow{width:26px;height:26px;border-radius:50%;background:#000}
.dot{width:11px;height:11px;border-radius:50%}
.btn-gold{left:516px;width:168px;height:55px;background:var(--gold);color:var(--white);font-family:"Roboto",sans-serif;font-weight:700;font-size:15px;text-align:center;line-height:55px}

/* course */
.course{left:0;top:3981px;width:1200px;height:466px;background:linear-gradient(180deg,#1a1a1a,#262626)}
.course-text{left:200px;width:800px;font-size:15.5px;line-height:27.5px;text-align:center;color:var(--white)}

/* contact */
.map{left:0;top:4446px;width:1200px;height:557px;background:linear-gradient(135deg,#eef0e6,#e3e9d9 45%,#eef0e6)}
.contact{left:112px;top:4553px;width:414px;height:341px;background:var(--navy);color:var(--white);padding:56px 38px 0}
.contact h2{font-family:"Roboto",sans-serif;font-weight:700;font-size:28px}
.contact p{font-size:17px;line-height:31px}
.footer{left:0;top:5002px;width:1200px;height:57px;background:var(--gold);color:var(--white);font-size:15px;font-weight:500;text-align:center;line-height:57px}
</style>
</head>
<body>

<!-- Hero -->
<div class="abs hero" role="img" aria-label="Meditating woman with glowing chakra light behind her, dark purple background"></div>
<div class="abs brand"><span class="brand-mark"></span>LON VARICK</div>
<div class="abs nav active" style="left:318px">HOME</div>
<div class="abs nav" style="left:415px">ABOUT</div>
<div class="abs nav" style="left:516px">LESSONS</div>
<div class="abs nav" style="left:637px">ONLINE COURSE</div>
<div class="abs nav" style="left:806px">CHAKRAS</div>
<div class="abs btn-contact">CONTACT US</div>

<h1 class="abs hero-title">KESTO 2025 — REWIRE YOUR BRAIN.<br>KESTO YOUR LIFE.</h1>
<p class="abs hero-sub">A 5-week journey to transformation through neuroscience, meditation &amp; emotional wellness.</p>

<div class="abs stat" style="left:110px"><h3>Kesto</h3><div class="by"></div><hr><p>Transformation through<br>neuroscience</p></div>
<div class="abs stat" style="left:362px"><h3>Kesto</h3><div class="by">by Lon Varick</div><hr><p>The Girl Who<br>Painted Her Sky</p></div>
<div class="abs stat" style="left:616px"><h3>Lon Varick</h3><div class="by"></div><hr><p>A journey of<br>self-healing</p></div>
<div class="abs stat" style="left:868px"><h3>AUD 4999</h3><div class="by"></div><hr><p>New online<br>course</p></div>

<!-- About our lesson -->
<h2 class="abs section-title" style="top:770px">ABOUT OUR LESSON</h2>
<p class="abs lede" style="top:842px">Lorem ipsum dolor sit amet, consectetur adipiscing elit, sed do eiusmod tempor incididunt utconsectetur adipiscing elit, sed do eiusmod tempor incididunt ut labore et dolore magna aliqua. Ut enim ad minim veniam, quis nostrud exercitation ullamco labore et dolore magna aliqua. Ut enim ad minim veniam, quisis nisi ut aliquip ex ea commodo consequat.</p>

<div class="abs lesson" style="left:110px;top:1007px;width:314px;height:319px;background:linear-gradient(160deg,#e9a452,#b0652c 55%,#3a2418)" role="img" aria-label="Woman smiling in warm sunset light">
  <b>Lesson 1</b><span>The Science of Meditation &amp; the Mind-Body Connection</span></div>
<div class="abs lesson navy" style="left:110px;top:1355px;width:314px;height:161px">
  <b>Lesson 2</b><span>Lon Varick’s Personal Healing &amp; Neuroplasticity</span></div>
<div class="abs lesson navy" style="left:454px;top:1009px;width:318px;height:160px">
  <b>Lesson 3</b><span>Emotional Stress and Disease</span></div>
<div class="abs lesson" style="left:454px;top:1196px;width:318px;height:318px;background:radial-gradient(circle at 50% 45%,#f6d9a0,#d07a2c 40%,#5a2a10 85%)" role="img" aria-label="Glowing lotus flower held in open hands">
  <b>Lesson 4</b><span>ZRM (Zonal Ribbon Merge)<br>Process</span></div>
<div class="abs lesson" style="left:807px;top:1009px;width:281px;height:505px;background:linear-gradient(180deg,#c54a9e,#6a2a80 25%,#c6622a 50%,#b38a1c 70%,#1d2a4a)" role="img" aria-label="Stacked candle lights in rainbow chakra colours">
  <b>Lesson 5</b><span>Solfeggio Frequencies &amp;<br>Chakra Healing</span></div>

<!-- Banner -->
<div class="abs" style="left:0;top:1665px;width:1200px;height:554px;background:radial-gradient(ellipse at 50% 45%,#e0b22a 0%,#a6782a 25%,#6a4a3a 55%,#3a2e2e 100%)" role="img" aria-label="Hands holding a yellow smiling plush ball"></div>
<div class="abs dot" style="left:584px;top:2153px;background:#fff"></div>
<div class="abs dot" style="left:604px;top:2153px;background:#fff"></div>

<!-- Chakra books -->
<h2 class="abs section-title" style="top:2318px">SEVEN CHAKRA MEDITATION BOOK</h2>
<p class="abs lede" style="top:2389px">Lorem ipsum dolor sit amet, consectetur adipiscing elit, sed do eiusmod tempor incididunt utconsectetur adipiscing elit, sed do eiusmod tempor incididunt ut labore et dolore magna aliqua</p>

<div class="abs arrow" style="left:38px;top:2689px"><svg width="26" height="26" viewBox="0 0 26 26"><path d="M15 8l-5 5 5 5" fill="none" stroke="#fff" stroke-width="2.2"/></svg></div>
<div class="abs arrow" style="left:1133px;top:2689px"><svg width="26" height="26" viewBox="0 0 26 26"><path d="M11 8l5 5-5 5" fill="none" stroke="#fff" stroke-width="2.2"/></svg></div>

<div class="abs book" style="left:110px">
  <div class="cover" role="img" aria-label="Book cover, red and cream torn paper" style="background:linear-gradient(180deg,#7a2a1c,#f2e6cc 45%,#e8d6a8 70%,#6a2418)"></div>
  <div class="cap"><h4>Sahasrara</h4><p>Crown Chakra(Spritual)</p></div></div>
<div class="abs book active" style="left:450px">
  <div class="cover" role="img" aria-label="Book cover, green torn paper" style="left:76px;top:40px;width:150px;height:210px;background:linear-gradient(180deg,#5a6a1a,#e6f7a0 45%,#c9e86a 70%,#4a5a14)"></div>
  <svg style="position:absolute;left:106px;top:282px" width="88" height="44" viewBox="0 0 88 44"><path d="M0 44A44 44 0 0 1 88 44Z" fill="#c0950f"/><ellipse cx="44" cy="28" rx="13" ry="7" fill="none" stroke="#fff" stroke-width="2"/><circle cx="44" cy="28" r="3" fill="#fff"/></svg>
  <div class="cap"><h4>Ajna</h4><p>Third Eye Chakra(Awareness)</p></div></div>
<div class="abs book" style="left:788px">
  <div class="cover" role="img" aria-label="Book cover, teal torn paper" style="background:linear-gradient(180deg,#1a7a4a,#c8f2e0 45%,#8ae6c4 70%,#146a40)"></div>
  <div class="cap"><h4>Vishuddha</h4><p>Throat Chakra(Communication)</p></div></div>

<p class="abs lede" style="top:2988px">Lorem ipsum dolor sit amet, consectetur adipiscing elit, sed do eiusmod tempor incididunt utconsectetur adipiscing elit, sed do eiusmod tempor incididunt ut labore et dolore magna aliqua</p>

<div class="abs" style="left:110px;top:3125px;width:978px;height:581px;background:linear-gradient(180deg,#c9b48f,#a7865e 40%,#7a5a4a 75%,#e6c79a)" role="img" aria-label="Group of smiling friends joining raised hands"></div>
<div class="abs dot" style="left:573px;top:3768px;background:var(--gold)"></div>
<div class="abs dot" style="left:594px;top:3768px;background:#bfc3cf"></div>
<div class="abs dot" style="left:615px;top:3768px;background:#bfc3cf"></div>
<div class="abs btn-gold" style="top:3834px">GET A QUOTE</div>

<!-- Online course -->
<div class="abs course" role="img" aria-label="Dark photo background of a person at a desk"></div>
<h2 class="abs section-title" style="top:4070px;color:var(--white)">NEW ONLINE COURSE</h2>
<p class="abs course-text" style="top:4136px;font-weight:600">This transformative program combines neuroscience, emotional wellness, and ancient meditation practices to guide users through a journey of self-healing.</p>
<p class="abs course-text" style="top:4219px">Lorem ipsum dolor sit amet, consectetur adipiscing elit, sed do eiusmod tempor incididunt utconsectetur adipiscing elit, sed do eiusmod tempor incididunt ut labore et dolore magna aliqua</p>
<svg class="abs" style="left:410px;top:4285px" width="80" height="80" viewBox="0 0 80 80"><path d="M8 4C0 30 20 58 70 55" fill="none" stroke="#c0950f" stroke-width="2"/><path d="M60 47l11 8-12 6" fill="none" stroke="#c0950f" stroke-width="2"/></svg>
<div class="abs btn-gold" style="top:4312px;height:52px;line-height:52px">GET STARTED</div>

<!-- Contact & map -->
<div class="abs map" role="img" aria-label="Road map of the region with a location pin"></div>
<svg class="abs" style="left:830px;top:4752px" width="24" height="32" viewBox="0 0 24 32"><path d="M12 31C12 31 2 18 2 11a10 10 0 0 1 20 0c0 7-10 20-10 20z" fill="#d42020"/><circle cx="12" cy="11" r="4" fill="#fff"/></svg>
<div class="abs contact">
  <h2>LON VARICK</h2>
  <p style="margin-top:14px">Working hours: Mon – Fri, 9:00 – 18:00</p>
  <p style="margin-top:28px">+1 555 014 2290</p>
  <p>hello@lonvarick.example</p>
  <p>Lon Varick, United States</p>
</div>
<div class="abs footer">Copyrights@2025.Lon Varick.All Rights Reserved</div>

</body>
</html>
```